HearthMile business card and stationary design

We are looking for a simple yet elegant design for our mortgage company business card and stationary.

The card should include:
Name (Marcus Pell)
Title (CEO)
Phone Number (919-555-0182)
Address (48 Birchwell Court, Suite 314, Fernbrook, OR 97402)
Email (email@hearthmile.example)
"NMLS" i.e. (NMLS 61947)
"Company NMLS" (Company NMLS 274615)

Contact Information for Business Card

See above

```html
<!DOCTYPE html>
<html lang="en">
<head>
<meta charset="utf-8">
<title>HearthMile Business Card</title>
<link href="https://fonts.googleapis.com/css2?family=Montserrat:wght@400;500;600&display=swap" rel="stylesheet">
<style>
  :root {
    --brand-blue: #2aa5db;
    --ink-dark: #1c2733;
    --ink-grey: #555b61;
    --card-white: #f4f4f3;
    --backdrop: #e9e9e8;
  }
  html, body {
    margin: 0;
    padding: 0;
    width: 1200px;
    height: 800px;
    overflow: hidden;
    background: var(--backdrop);
    font-family: "Montserrat", Arial, sans-serif;
  }
  .stage {
    position: relative;
    width: 1200px;
    height: 800px;
  }
  .card {
    position: absolute;
    width: 525px;
    height: 300px;
    top: 250px;
    box-sizing: border-box;
    box-shadow: 0 2px 6px rgba(0,0,0,0.08);
  }
  .card-front {
    left: 50px;
    background: var(--card-white);
  }
  .card-back {
    left: 625px;
    background: var(--brand-blue);
    display: flex;
    align-items: center;
    justify-content: center;
  }
  .wordmark {
    font-weight: 500;
    letter-spacing: 0.5px;
    line-height: 1;
  }
  .card-front .wordmark {
    position: absolute;
    left: 40px;
    top: 42px;
    font-size: 40px;
    color: var(--brand-blue);
  }
  .card-back .wordmark {
    font-size: 58px;
    color: #ffffff;
  }
  .license-bar {
    position: absolute;
    left: 14px;
    top: 128px;
    width: 3px;
    height: 20px;
    background: var(--ink-dark);
  }
  .license {
    position: absolute;
    left: 36px;
    top: 128px;
    font-size: 11.5px;
    line-height: 17px;
    color: var(--ink-grey);
  }
  .contact {
    position: absolute;
    left: 262px;
    top: 150px;
    font-size: 11.5px;
    line-height: 16px;
    color: var(--ink-grey);
  }
  .contact .name {
    font-size: 21px;
    font-weight: 600;
    letter-spacing: 1px;
    text-transform: uppercase;
    color: var(--brand-blue);
    line-height: 22px;
  }
  .contact .title {
    margin-bottom: 6px;
  }
  .contact .line {
    display: flex;
    align-items: center;
    gap: 4px;
  }
  .contact svg {
    width: 10px;
    height: 10px;
    flex: none;
  }
</style>
</head>
<body>
<main class="stage">
  <section class="card card-front">
    <div class="wordmark">HearthMile</div>
    <div class="license-bar"></div>
    <div class="license">
      <div>NMLS 61947</div>
      <div>Company NMLS 274615</div>
    </div>
    <div class="contact">
      <div class="name">Marcus Pell</div>
      <div class="title">CEO</div>
      <div>48 Birchwell Court,</div>
      <div>Suite 314, Fernbrook, OR 97402</div>
      <div class="line">
        <svg viewBox="0 0 10 10" aria-hidden="true"><path d="M2 1 L4 1 L4.6 3 L3.4 3.8 Q4.3 5.8 6.2 6.6 L7 5.4 L9 6 L9 8 Q9 9 8 9 Q1 8.6 1 2 Q1 1 2 1 Z" fill="var(--brand-blue)"/></svg>
        <span>919-555-0182</span>
      </div>
      <div class="line">
        <svg viewBox="0 0 10 10" aria-hidden="true"><rect x="0.8" y="2" width="8.4" height="6" fill="none" stroke="var(--brand-blue)" stroke-width="1"/><path d="M0.8 2 L5 5.4 L9.2 2" fill="none" stroke="var(--brand-blue)" stroke-width="1"/></svg>
        <span>email@hearthmile.example</span>
      </div>
    </div>
  </section>
  <section class="card card-back">
    <div class="wordmark">HearthMile</div>
  </section>
</main>
</body>
</html>
```